VTMB site redesign

Please redesign a home page with content provided. PSD only - no coding
Can use any images from Snapwelder.com

Please create a site design that more clearly illustrates the client's services and expertise. We are looking for a high-end design.

Any images used must be generic or of Dallas TX.

Fonts: Any
Colors: Match to logo
Look: Modern - Professional

Target Market(s)

medium-large business owners

Number of Pages Required

1 page

Font styles to use
Serif
Sans Serif

Requirements
Must have
• cohesive professional design
• high end look
• Match to logo

```html
<!DOCTYPE html>
<html lang="en">
<head>
<meta charset="utf-8">
<title>VTMB – Vantemore Commercial Realty Group</title>
<link href="https://fonts.googleapis.com/css2?family=Lora:wght@400;700&family=Open+Sans:wght@400;600;700&display=swap" rel="stylesheet">
<style>
:root{
  --red:#a8000f;
  --red-dark:#8e000c;
  --card:#ececec;
  --text:#444;
  --muted:#666;
  --light:#f0f0f0;
  --footer:#2b2b2b;
  --footer-bottom:#1f1f1f;
  --white:#fff;
  --serif:'Lora', Georgia, serif;
  --sans:'Open Sans', Arial, sans-serif;
}
*{margin:0;padding:0;box-sizing:border-box}
html,body{width:1200px;height:3782px;overflow:hidden;background:var(--white)}
body{position:relative;font-family:var(--sans);color:var(--text)}
.abs{position:absolute}
.center{left:0;width:1200px;text-align:center}

/* header */
.site-header{top:0;left:0;width:1200px;height:155px;background:var(--red)}
.brand{left:135px;top:22px;color:var(--white);font-family:var(--serif)}
.brand-name{font-size:46px;font-weight:700;letter-spacing:3px;line-height:1}
.brand-tag{font-family:var(--sans);font-size:9px;letter-spacing:1.4px;margin-top:10px;font-weight:600}
.phone{right:135px;top:38px;color:var(--white);font-family:var(--serif);font-size:17px;display:flex;align-items:center;gap:8px}
.main-nav{right:135px;top:96px;display:flex;gap:30px}
.main-nav a{color:var(--white);text-decoration:none;font-size:13px;font-weight:600;letter-spacing:.4px}
.main-nav a.active{border-bottom:1px solid var(--white);padding-bottom:3px}

/* hero */
.hero{top:155px;left:0;width:1200px;height:505px;background:linear-gradient(180deg,#7f8fa6 0%,#c59a86 45%,#5b4b52 70%,#2a2a33 100%)}
.hero-shade{left:0;top:0;width:100%;height:100%;background:linear-gradient(180deg,rgba(0,0,0,0) 55%,rgba(0,0,0,.55) 100%)}
.hero-title{left:135px;top:578px;color:var(--white);font-family:var(--serif);font-weight:700;font-size:23px;letter-spacing:.6px}
.hero-sub{left:135px;top:612px;color:#eee;font-size:16px}
.hero-arrow{top:380px;color:var(--white);font-size:16px}

/* why */
.section-title{font-family:var(--serif);font-weight:400;color:var(--red);font-size:30px;letter-spacing:.5px}
.card{width:443px;height:161px;background:var(--card);padding:22px 26px 0 112px}
.card svg{position:absolute;left:26px;top:24px}
.card h3{font-family:var(--serif);font-weight:400;font-size:19px;color:#333;margin-bottom:8px}
.card p{font-size:10px;line-height:1.6;color:var(--muted);width:300px}
.card .more{position:absolute;left:112px;top:128px;font-size:9px;color:#555;text-decoration:underline;letter-spacing:.3px}

/* red bands */
.band svg{display:block}
.band-text{color:var(--white);font-family:var(--serif);font-size:23px;line-height:1.5}
.btn{display:inline-block;font-family:var(--serif);font-size:21px;padding:11px 22px;letter-spacing:.5px}
.btn-white{background:var(--white);color:var(--red)}
.btn-red{background:var(--red);color:var(--white)}

/* team */
.team-intro{left:140px;width:920px;text-align:center;font-size:13.5px;line-height:1.75;color:var(--text)}
.member{width:171px;text-align:center}
.member .photo{width:171px;height:194px;background:linear-gradient(160deg,#bdbdbd,#6f6f6f)}
.member h4{font-family:var(--serif);font-weight:400;color:var(--red);font-size:14px;margin-top:22px}
.member span{display:block;font-size:11px;color:#555;line-height:1.5;margin-top:4px}

/* testimonials */
.quote{left:150px;width:900px;text-align:center;color:var(--white);font-family:var(--serif);font-size:15px;line-height:1.75}
.dots{display:flex;gap:10px;justify-content:center}
.dots i{width:10px;height:10px;border-radius:50%;background:#5e0008;display:block}
.dots i.on{background:var(--white)}

/* articles */
.article{left:134px;top:3163px;width:932px;height:197px;background:var(--white);text-align:center;padding-top:28px}
.article h3{font-family:var(--serif);font-weight:400;font-size:21px;color:#222}
.article time{display:block;font-family:var(--serif);font-size:13px;margin:10px 0 12px;color:#333}
.article p{font-size:13px;line-height:1.7;color:#555;padding:0 48px}
.pager{width:22px;height:22px;border:1px solid #555;display:flex;align-items:center;justify-content:center}

/* footer */
.footer-col h5{font-family:var(--serif);font-weight:400;font-size:17px;color:#eee;margin-bottom:14px}
.footer-col p{font-size:12px;color:#aaa;line-height:1.85}
.legal a{display:block;font-size:12px;color:#aaa;text-align:right;line-height:2.2;text-decoration:none}
.foot-nav{left:134px;top:3712px;font-size:10px;color:#999}
.copyright{left:134px;top:3738px;font-size:10px;color:#888}
.socials{right:134px;top:3718px;display:flex;gap:20px}
.socials i{width:14px;height:14px;border-radius:50%;background:#888;display:block}
</style>
</head>
<body>

<header class="abs site-header">
  <div class="abs brand">
    <div class="brand-name">VTMB</div>
    <div class="brand-tag">CORPORATE SPACE ADVISORS</div>
  </div>
  <div class="abs phone">
    <svg width="12" height="18" viewBox="0 0 12 18"><rect x="1" y="1" width="10" height="16" rx="2" fill="none" stroke="#fff" stroke-width="1.6"/><circle cx="6" cy="14" r="1" fill="#fff"/></svg>
    Call Today : 214-555-0142
  </div>
  <nav class="abs main-nav">
    <a class="active">SERVICES</a><a>ABOUT VTMB</a><a>BLOG</a><a>MARKET NEWS</a><a>CONTACT US</a>
  </nav>
</header>

<section class="abs hero" role="img" aria-label="Photograph of the downtown Dallas skyline at dusk">
  <div class="abs hero-shade"></div>
</section>
<div class="abs hero-arrow" style="left:8px">&#9664;</div>
<div class="abs hero-arrow" style="right:8px">&#9654;</div>
<h1 class="abs hero-title">PROFESSIONAL OFFICE AND WAREHOUSE LEASING</h1>
<p class="abs hero-sub">Fast-track your search with tenant reps that only serve you, and specialize in the DFW area</p>

<svg class="abs" style="left:0;top:655px" width="1200" height="50" viewBox="0 0 1200 50"><polygon points="0,5 1200,5 1200,45 0,22" fill="#a8000f"/></svg>

<h2 class="abs center section-title" style="top:774px">WHY TENANT REPRESENTATION?</h2>

<article class="abs card" style="left:134px;top:842px">
  <svg width="56" height="40" viewBox="0 0 56 40" fill="none" stroke="#a8000f" stroke-width="2"><path d="M2 12l10-6 10 4 8-4 10 2 14 6"/><path d="M12 26l10 8 6-2 8 4 6-6 10-8"/><path d="M22 16l8 6 6-4"/></svg>
  <h3>Relationships</h3>
  <p>Save time by trusting VTMB year after year to find the right location for you. Once we've worked together, we know what you need, and you can keep your budget details private.</p>
  <span class="more">READ MORE</span>
</article>
<article class="abs card" style="left:622px;top:842px">
  <svg width="44" height="48" viewBox="0 0 44 48" fill="none" stroke="#a8000f" stroke-width="2"><rect x="4" y="4" width="36" height="42" rx="2"/><path d="M10 14l3 3 5-6M10 26l3 3 5-6M10 38l3 3 5-6M24 15h10M24 27h10M24 39h10"/></svg>
  <h3>Access to More</h3>
  <p>We have no agreements or personal incentives for specific properties, so we can always show you the offices that are right for you.</p>
  <span class="more">READ MORE</span>
</article>
<article class="abs card" style="left:134px;top:1051px">
  <svg width="48" height="48" viewBox="0 0 48 48" fill="none" stroke="#a8000f" stroke-width="2"><polygon points="24,2 30,10 40,8 40,18 46,24 40,30 40,40 30,38 24,46 18,38 8,40 8,30 2,24 8,18 8,8 18,10"/><polygon points="24,14 27,21 34,21 28,26 31,33 24,29 17,33 20,26 14,21 21,21"/></svg>
  <h3>Free To You</h3>
  <p>You pay us nothing. We get our commission from the property being leased.</p>
  <span class="more">READ MORE</span>
</article>
<article class="abs card" style="left:622px;top:1051px">
  <svg width="50" height="44" viewBox="0 0 50 44" fill="none" stroke="#a8000f" stroke-width="2"><rect x="2" y="10" width="46" height="32" rx="3"/><path d="M18 10V4h14v6M2 22h46M22 20h6v6h-6z"/></svg>
  <h3>Customized Service</h3>
  <p>Aside from saving you the time of repeating what your needs are to each new location, we also provide a report of the places you've seen, so it's easier to share and make a decision.</p>
  <span class="more">READ MORE</span>
</article>

<svg class="abs band" style="left:0;top:1310px" width="1200" height="360" viewBox="0 0 1200 360"><polygon points="0,0 1200,60 1200,305 0,355" fill="#a8000f"/></svg>
<p class="abs center band-text" style="top:1412px">If you need to find office or warehouse space in the Dallas Fort Worth area, the<br>team at VTMB has the experience you need.</p>
<div class="abs center" style="top:1502px"><span class="btn btn-white">SPACE CALCULATOR</span></div>

<h2 class="abs center section-title" style="top:1740px">MEET THE TEAM</h2>
<p class="abs team-intro" style="top:1792px">At VTMB we believe that you deserve the best professional advice and personal service with your commercial real estate negotiations. By choosing VTMB as your tenant reps in the Dallas/Fort Worth area, you will receive the assistance of accomplished and experienced commercial real estate brokers and salespeople who are licensed by the State Realty Licensing Board to practice in Texas since 1982.</p>

<div class="abs member" style="left:305px;top:1898px">
  <div class="photo" role="img" aria-label="Portrait photo of Graham H. Vantemore"></div>
  <h4>Graham H. Vantemore</h4><span>Founder and President</span>
</div>
<div class="abs member" style="left:514px;top:1898px">
  <div class="photo" role="img" aria-label="Portrait photo of Mark Peyton Mills"></div>
  <h4>Mark Peyton Mills</h4><span>Senior Director, Commercial<br>Property Specialist</span>
</div>
<div class="abs member" style="left:726px;top:1898px">
  <div class="photo" role="img" aria-label="Portrait photo of Martin Avery Mills"></div>
  <h4>Martin Avery Mills</h4><span>Jr., Associate, Tenant Rep<br>Specialist</span>
</div>

<svg class="abs band" style="left:0;top:2240px" width="1200" height="390" viewBox="0 0 1200 390"><polygon points="0,55 1200,0 1200,385 0,340" fill="#a8000f"/></svg>
<h2 class="abs center" style="top:2352px;font-family:var(--serif);font-weight:400;color:#fff;font-size:30px;letter-spacing:.5px">TESTIMONIALS</h2>
<p class="abs quote" style="top:2402px">"The real estate team at VTMB has decades of experience in Commercial. One advantage of VTMB is they know all the properties that are about to become available, BEFORE they are available. They have the inside track on properties and they watch your back at the negotiating table. Very impressive with a polished approach. Let the team run with your next project and you won't be disappointed."</p>
<p class="abs center" style="top:2520px;color:#fff;font-family:var(--serif);font-size:14px">- Colin Bradley Dorsey -</p>
<div class="abs center dots" style="top:2558px"><i class="on"></i><i></i><i></i><i></i></div>

<p class="abs center" style="top:2762px;font-family:var(--serif);font-size:26px;color:#333;line-height:1.45">Whether your lease is expiring soon, or you're just starting your search,<br>VTMB can help you find the perfect space.</p>
<div class="abs center" style="top:2852px"><span class="btn btn-red">MAKE AN APPOINTMENT</span></div>

<svg class="abs" style="left:0;top:2990px" width="1200" height="520" viewBox="0 0 1200 520"><polygon points="0,0 1200,45 1200,440 0,500" fill="#f0f0f0"/></svg>
<div class="abs pager" style="left:411px;top:3113px"><svg width="8" height="10" viewBox="0 0 8 10"><path d="M6 1L2 5l4 4" fill="none" stroke="#555" stroke-width="1.5"/></svg></div>
<h2 class="abs center section-title" style="top:3105px">RECENT ARTICLES</h2>
<div class="abs pager" style="left:764px;top:3113px"><svg width="8" height="10" viewBox="0 0 8 10"><path d="M2 1l4 4-4 4" fill="none" stroke="#555" stroke-width="1.5"/></svg></div>
<article class="abs article">
  <h3>Phasellus nisl est, condimentum vitae faucibus in, sollicitudin</h3>
  <time>7 May, 2018</time>
  <p>Aenean sed quam non sapien faucibus consequat vitae sit amet orci. Praesent quis risus mi. In mollis nulla in pulvinar dictum. Vivamus interdum sagittis felis, ut dapibus ligula feugiat ac. In dictum sapien eu tellus finibus fermentum. Aenean faucibus lacus ut mollis commodo. Donec vestibulum odio sem, ac laoreet massa ullamcorper id.</p>
</article>

<svg class="abs" style="left:0;top:3425px" width="1200" height="357" viewBox="0 0 1200 357"><polygon points="0,65 1200,5 1200,357 0,357" fill="#2b2b2b"/><rect x="0" y="262" width="1200" height="95" fill="#1f1f1f"/></svg>
<div class="abs footer-col" style="left:134px;top:3530px">
  <h5>Contact Us</h5>
  <p>412 Cedar Brook Avenue, Suite 310, Irving, TX 75038<br>Tel: 214-555-0142 &nbsp;|&nbsp; Fax: 214-555-0187<br>Email : info@vtmb.com</p>
</div>
<div class="abs footer-col legal" style="right:134px;top:3530px">
  <h5>State Realty Licensing Board Mandated Disclosure Notice</h5>
  <a>&#128462; State Realty Licensing Board Information About Brokerage Services</a>
  <a>&#128462; State Realty Licensing Board Consumer Protection Notice</a>
</div>
<div class="abs foot-nav">Services &nbsp;|&nbsp; About VTMB &nbsp;|&nbsp; Blog &nbsp;|&nbsp; Market News &nbsp;|&nbsp; Contact Us</div>
<div class="abs copyright">Copyright © 2018 Vantemore Commercial Real Estate Group. All rights reserved.</div>
<div class="abs socials" aria-label="Social links"><i></i><i></i><i></i></div>

</body>
</html>
```